Tradelume.ai

Australian based application building technology company. website (tradelume.ai) servicing the retail and shopping industries, IoT
Similar services to https://vextrio.com/.
Logo attached

Target Market(s)

Technology Retail

Industry/Entity Type

It Company

Number of Pages Required

2 page

Font styles to use
Other font styles liked:
• We will supply

Colors
ec1f27

Requirements
Must have
• responsive, extra small, small, medium, large, wide
Nice to have
• Modern, sophisticated, current and ON trende
Should not have
• Over saturation, keep it simple, smart and easy navigation

```html
<!DOCTYPE html>
<html lang="en">
<head>
<meta charset="utf-8">
<title>Tradelume — Retail &amp; IoT Applications</title>
<link rel="stylesheet" href="https://fonts.googleapis.com/css2?family=Roboto:wght@300;400;500;700&display=swap">
<style>
:root{
  --red:#ec1f27;
  --red-dark:#c4121a;
  --ink:#333;
  --muted:#777;
  --light:#f4f5f7;
  --dark:#1f1f1f;
  --white:#fff;
}
*{box-sizing:border-box;margin:0;padding:0}
html,body{width:1200px;height:3429px;overflow:hidden}
body{font-family:"Roboto",Arial,sans-serif;color:var(--ink);background:var(--white);position:relative}
.abs{position:absolute}
.wordmark{font-family:"Roboto",Arial,sans-serif;font-weight:400;letter-spacing:1px;display:flex;align-items:center;gap:12px;white-space:nowrap}
.wordmark .dot{border-radius:50%;background:var(--red);display:inline-block}
.btn{position:absolute;display:flex;align-items:center;justify-content:center;font-size:12px;font-weight:500;text-transform:uppercase;letter-spacing:.3px;white-space:nowrap}
.btn-red{background:var(--red);color:var(--white);border-radius:2px}
.btn-ghost{border:1px solid rgba(255,255,255,.8);color:var(--white);border-radius:2px}
.para{font-size:11.5px;line-height:23px;color:var(--muted)}

/* header */
.site-header{left:0;top:0;width:1200px;height:92px;background:var(--white)}
.site-header .wordmark{position:absolute;left:87px;top:26px;font-size:31px;color:var(--red)}
.nav{position:absolute;right:90px;top:0;height:92px;display:flex;align-items:center;gap:46px;font-size:12px;text-transform:uppercase;color:#333}
.nav .active{color:var(--red)}
.search{position:absolute;right:30px;top:23px;width:46px;height:46px;border:1px solid var(--red);border-radius:50%}

/* hero */
.hero{left:0;top:92px;width:1200px;height:502px;background:radial-gradient(circle at 20% 40%,#d9a24a 0,#6d5a3a 10%,#26303d 32%,#152131 60%,#0c141f 100%)}
.hero .wordmark{position:absolute;left:0;width:1200px;top:130px;justify-content:center;font-size:52px;color:var(--white)}
.hero .lead{position:absolute;left:270px;width:660px;top:222px;text-align:center;font-size:12px;line-height:24px;color:#e4e6ea}
.hero .arrow{position:absolute;top:226px;width:52px;height:52px;border:2px solid var(--white);border-radius:50%}

/* welcome */
.welcome h2{position:absolute;left:0;width:1200px;top:650px;text-align:center;color:var(--red);font-size:20px;font-weight:500}
.welcome .intro{position:absolute;left:250px;width:700px;top:688px;text-align:center}
.feature{position:absolute;top:766px;width:330px;text-align:center}
.feature .icon{width:114px;height:114px;border-radius:50%;margin:0 auto;display:flex;align-items:center;justify-content:center}
.feature h3{font-size:14px;font-weight:500;margin-top:25px;text-transform:uppercase}
.feature .para{margin-top:6px}

/* split rows */
.band-grey{left:0;width:1200px;background:var(--light)}
.row-title{font-size:20px;font-weight:300;line-height:34px;color:#555}
.mock{position:absolute}
.video-panel{position:absolute;left:85px;width:500px;height:322px;background:var(--red-dark)}

/* about */
.about h2{position:absolute;left:0;width:1200px;top:2340px;text-align:center;font-size:23px;font-weight:300;color:#555}
.about .para{position:absolute;left:230px;width:740px;top:2382px;text-align:center}
.browser{position:absolute;left:331px;top:2498px;width:538px;height:318px;background:#e4e6ea;border-radius:4px 4px 0 0;padding:22px 12px 0}
.browser .screen{background:var(--white);width:100%;height:100%;display:flex;align-items:center;justify-content:center}

/* cta */
.cta{left:0;top:2816px;width:1200px;height:304px;background:var(--red)}
.cta h2{position:absolute;left:0;width:1200px;top:68px;text-align:center;color:var(--white);font-size:22px;font-weight:400}
.cta p{position:absolute;left:220px;width:760px;top:112px;text-align:center;color:#fde;font-size:11.5px;line-height:24px}

/* footer */
.footer{left:0;top:3120px;width:1200px;height:309px;background:var(--dark);color:#eee}
.footer h4{font-size:16px;font-weight:500;text-transform:uppercase;letter-spacing:.4px;color:var(--white)}
.footer .col{position:absolute;top:40px;font-size:11.5px;line-height:18px}
.contact-list li{list-style:none;display:flex;gap:14px;align-items:flex-start;margin-top:14px}
.contact-list svg{flex:none;margin-top:3px}
.email-field{margin-top:14px;width:224px;height:32px;background:var(--white);color:#999;font-size:11px;padding:0 12px;display:flex;align-items:center}
.subscribe{margin-top:12px;width:74px;height:24px;background:var(--red);color:var(--white);font-size:10px;display:flex;align-items:center;justify-content:center;text-transform:uppercase}
.social{display:flex;gap:10px;margin-top:20px}
.social span{width:32px;height:32px;border:1px solid #ddd;border-radius:50%}
.copyright{position:absolute;left:0;width:1200px;top:268px;text-align:center;font-size:11px;color:#ccc}
</style>
</head>
<body>

<header class="abs site-header">
  <div class="wordmark"><span class="dot" style="width:30px;height:30px"></span>TRADELUME</div>
  <nav class="nav">
    <span class="active">Home</span><span>About Us</span><span>Services</span><span>Products</span><span>Resources</span><span>Contact Us</span>
  </nav>
  <div class="search">
    <svg width="46" height="46" viewBox="0 0 46 46"><circle cx="22" cy="22" r="5" fill="none" stroke="#ec1f27" stroke-width="2"/><line x1="26" y1="26" x2="29" y2="29" stroke="#ec1f27" stroke-width="2"/></svg>
  </div>
</header>

<section class="abs hero" role="img" aria-label="Hand holding a glowing digital retail analytics interface">
  <div class="wordmark"><span class="dot" style="width:48px;height:48px;background:#fff"></span>TRADELUME</div>
  <p class="lead">Sed ut perspiciatis unde omnis iste natus error sit voluptatem accusantium doloremque laudantium, totam rem aperiam, eaque ipsa quae ab illo inventore veritatis et quasi architecto beatae vitae dicta sunt explicabo.</p>
  <a class="btn btn-ghost" style="left:496px;top:297px;width:208px;height:41px">Click here for more info</a>
  <span class="arrow" style="left:24px"><svg width="48" height="48" viewBox="0 0 48 48"><polyline points="27,16 19,24 27,32" fill="none" stroke="#fff" stroke-width="2.5"/></svg></span>
  <span class="arrow" style="left:1122px"><svg width="48" height="48" viewBox="0 0 48 48"><polyline points="21,16 29,24 21,32" fill="none" stroke="#fff" stroke-width="2.5"/></svg></span>
</section>

<section class="welcome">
  <h2>WELCOME TO TRADE LUME</h2>
  <p class="para intro">Sed ut perspiciatis unde omnis iste natus error sit voluptatem accusantium doloremque laudantium, totam rem aperiam, eaque ipsa quae ab illo inventore veritatis et quasi architecto beatae vitae dicta sunt explicabo.</p>

  <div class="feature" style="left:86px">
    <div class="icon" style="background:var(--red);box-shadow:0 0 0 5px #fff,0 0 0 6px var(--red)">
      <svg width="52" height="52" viewBox="0 0 52 52" fill="none" stroke="#fff" stroke-width="2.5"><rect x="10" y="18" width="32" height="28" rx="2"/><path d="M18 18v-5a8 8 0 0 1 16 0v5"/></svg>
    </div>
    <h3 style="color:var(--red)">Retail</h3>
    <p class="para">Sed ut perspiciatis unde omnis iste natus error sit voluptatem accusantium doloremque laudantium, beatae vitae dicta sunt explicabo.</p>
  </div>

  <div class="feature" style="left:436px">
    <div class="icon" style="background:#6a6a6a;box-shadow:0 0 0 5px #fff,0 0 0 6px #6a6a6a">
      <svg width="56" height="56" viewBox="0 0 56 56" fill="none" stroke="#fff" stroke-width="2.5"><path d="M8 22h40l-4-10H12z"/><rect x="12" y="22" width="32" height="22"/><rect x="23" y="30" width="10" height="14" fill="#fff"/></svg>
    </div>
    <h3>Shopping Industries</h3>
    <p class="para">Sed ut perspiciatis unde omnis iste natus error sit voluptatem accusantium doloremque laudantium, beatae vitae dicta sunt explicabo.</p>
  </div>

  <div class="feature" style="left:786px">
    <div class="icon" style="background:var(--red);box-shadow:0 0 0 5px #fff,0 0 0 6px var(--red)">
      <svg width="56" height="56" viewBox="0 0 56 56" fill="none" stroke="#fff" stroke-width="2.5"><path d="M16 30a9 9 0 0 1 2-17 11 11 0 0 1 20 0 9 9 0 0 1 2 17z"/><rect x="14" y="36" width="10" height="10"/><rect x="32" y="36" width="10" height="10"/></svg>
    </div>
    <h3 style="color:var(--red)">IoT Firms</h3>
    <p class="para">Sed ut perspiciatis unde omnis iste natus error sit voluptatem accusantium doloremque laudantium, beatae vitae dicta sunt explicabo.</p>
  </div>
</section>

<section class="abs band-grey" style="top:1047px;height:427px">
  <div class="mock" role="img" aria-label="Two smartphones showing the shopping app with store map and product search" style="left:149px;top:27px;width:331px;height:400px;background:linear-gradient(180deg,#e9e9ea 0,#f7f7f7 20%,#d6282e 22%,#f3f3f3 30%,#e6e6e6 100%);border-radius:28px 28px 0 0"></div>
  <div class="abs" style="left:530px;top:103px;width:560px">
    <h3 class="row-title">Sed ut perspiciatis unde omnis iste natus error sit volup tatem accusantium doloremque</h3>
    <p class="para" style="margin-top:18px">Sed ut perspiciatis unde omnis iste natus error sit voluptatem accusantium doloremque lauda ntium, totam rem aperiam, eaque ipsa quae ab illo inventore veritatis et quasi architecto bea tae vitae dicta sunt explicabo. Nemo enim ipsam voluptatem quia voluptas sit aspernatur aut odit aut fugit, sed quia consequuntur magni dolores</p>
  </div>
  <a class="btn btn-red" style="left:530px;top:315px;width:140px;height:42px">Read More</a>
</section>

<section class="abs" style="left:0;top:1474px;width:1200px;height:412px">
  <div class="abs" style="left:87px;top:108px;width:520px">
    <h3 class="row-title">Sed ut perspiciatis unde omnis iste natus error sit volup tatem accusantium doloremque</h3>
    <p class="para" style="margin-top:18px">Sed ut perspiciatis unde omnis iste natus error sit voluptatem accusantium doloremque lauda ntium, totam rem aperiam, eaque ipsa quae ab illo inventore veritatis et quasi architecto bea tae vitae dicta sunt explicabo. Nemo enim ipsam voluptatem quia voluptas sit aspernatur aut odit aut fugit, sed quia consequuntur magni dolores</p>
  </div>
  <a class="btn btn-red" style="left:87px;top:316px;width:138px;height:42px">Read More</a>
  <div class="mock" role="img" aria-label="Laptop displaying an illustration of an app being built" style="left:613px;top:80px;width:500px;height:275px;background:linear-gradient(180deg,#cfd1d4 0,#f6f6f6 8%,#eef2f4 85%,#b9bcc0 92%,#d9dbde 100%);border-radius:14px 14px 4px 4px"></div>
</section>

<section class="abs band-grey" style="top:1886px;height:423px">
  <div class="video-panel" style="top:50px">
    <div class="abs" role="img" aria-label="Hand holding a phone showing the shopping app" style="left:22px;top:28px;width:170px;height:205px;background:linear-gradient(160deg,#f1d9c8,#d9b5a0)"></div>
    <svg class="abs" style="left:218px;top:140px" width="62" height="46" viewBox="0 0 62 46"><rect width="62" height="46" rx="10" fill="#ec1f27" stroke="#fff" stroke-width="2"/><polygon points="25,14 40,23 25,32" fill="#fff"/></svg>
    <ul class="abs" style="left:250px;top:72px;list-style:none;color:#fff;font-size:13px;line-height:63px">
      <li>● &nbsp;Establish first contact in seconds</li>
      <li style="padding-left:42px">Interact immediately and promote</li>
      <li>● &nbsp;Analytics for real-time sales</li>
    </ul>
    <p class="abs" style="left:26px;top:245px;width:170px;text-align:center;color:#fff;font-size:13px;line-height:18px">A Personal Shopper in every customers hand</p>
    <p class="abs" style="left:270px;top:246px;color:#fff;font-size:40px;font-weight:400">tradelume</p>
  </div>
  <div class="abs" style="left:642px;top:88px;width:470px">
    <h3 class="row-title">Sed ut perspiciatis unde omnis iste natus</h3>
    <p class="para" style="margin-top:14px">Sed ut perspiciatis unde omnis iste natus error sit voluptatem accusantium dolor emque laudantium, totam rem aperiam, eaque ipsa quae ab illo inventore veritatis et quasi architecto beatae vitae dicta sunt explicabo. Nemo enim ipsam voluptatem quia voluptas sit aspernatur aut odit aut fugit, sed quia consequuntur magni dolores eos qui ratione voluptatem sequi nesciunt.</p>
  </div>
  <a class="btn btn-red" style="left:642px;top:293px;width:140px;height:42px">Read More</a>
</section>

<section class="about">
  <h2>About Trade Lume</h2>
  <p class="para">Sed ut perspiciatis unde omnis iste natus error sit voluptatem accusantium doloremque laudantium, totam rem aperiam, eaque ipsa quae ab illo inventore veritatis et quasi architecto beatae vitae dicta sunt explicabo. Nemo enim ipsam voluptatem quia voluptas sit aspernatur aut odit aut fugit, sed quia consequuntur magni dolores eos qui ratione voluptatem sequi nesciunt.</p>
  <div class="browser">
    <svg class="abs" style="left:10px;top:7px" width="40" height="8"><circle cx="4" cy="4" r="3" fill="#fff"/><circle cx="14" cy="4" r="3" fill="#fff"/><circle cx="24" cy="4" r="3" fill="#fff"/></svg>
    <div class="screen"><div class="wordmark" style="font-size:44px;color:var(--red)"><span class="dot" style="width:42px;height:42px"></span>TRADELUME</div></div>
  </div>
</section>

<section class="abs cta">
  <h2>Ready to get started?</h2>
  <p>Sed ut perspiciatis unde omnis iste natus error sit voluptatem accusantium dolor emque laudantium, totam rem aperiam, eaque ipsa quae ab illo inventore veritatis et quasi architecto beatae vitae dicta sunt explicabo</p>
  <a class="btn btn-ghost" style="left:480px;top:188px;width:240px;height:41px">Click here for more info</a>
</section>

<footer class="abs footer">
  <div class="wordmark abs" style="left:105px;top:117px;font-size:34px;color:#fff"><span class="dot" style="width:32px;height:32px;background:#fff"></span>TRADELUME</div>

  <div class="col" style="left:418px;width:210px">
    <h4>Contact Us</h4>
    <ul class="contact-list">
      <li><svg width="12" height="12" viewBox="0 0 12 12" fill="#fff"><path d="M2 1h3l1 3-2 1a7 7 0 0 0 3 3l1-2 3 1v3c-6 0-9-3-9-9z"/></svg>(02)-555-0184 (Phone)</li>
      <li><svg width="12" height="12" viewBox="0 0 12 12" fill="#fff"><rect x="1" y="4" width="10" height="6"/><rect x="3" y="1" width="6" height="3"/></svg>(02)-555-0185 (Fax)</li>
      <li><svg width="12" height="12" viewBox="0 0 12 12" fill="#fff"><rect x="1" y="2" width="10" height="8"/><polyline points="1,2 6,7 11,2" fill="none" stroke="#1f1f1f"/></svg><span style="text-decoration:underline">info@tradelume.ai</span></li>
      <li><svg width="12" height="12" viewBox="0 0 12 12" fill="#fff"><path d="M6 1a4 4 0 0 1 4 4c0 3-4 7-4 7S2 8 2 5a4 4 0 0 1 4-4z"/></svg>Unit #4, 2210 Harbour Lane Sample City NSW</li>
    </ul>
  </div>

  <div class="col" style="left:665px;width:240px">
    <h4>Newsletter</h4>
    <p style="margin-top:14px;width:200px">Register Your email address to get information about us</p>
    <div class="email-field">Email Address</div>
    <div class="subscribe">Subscribe</div>
  </div>

  <div class="col" style="left:940px;width:180px">
    <h4>Follow Us</h4>
    <p style="margin-top:14px;font-size:10.5px">Lorem ipsum dolor sit amet, conse ctetur adipiscing elit. Nulla in purus nibh. Donec ornare</p>
    <div class="social"><span></span><span></span><span></span><span></span></div>
  </div>

  <p class="copyright">© Copyright 2017 Trade Lume. All rights reserved</p>
</footer>

</body>
</html>
```